Tabloid Magazine Flyer Class Action Lawsuit

Create a bold, 2-page 8.5" x 11" flyer with the look and feel of a tabloid exposé — loud, sensational, and impossible to ignore. Use bold fonts, dramatic headlines, and high-contrast colors (red, black, white, deep blue). Fill every inch of space — no white space, no subtlety. Use the provided images prominently. Page 1 should grab attention with a shocking headline, impactful image, and strong call to action. Page 2 should stack bold subheadings and explosive bullet points. Emphasize urgency, outrage, and grassroots power. This flyer is meant to rally a community.
Updates

Need to extend because we haven't received a design that meets our needs

Target Market(s)

All instructions and content are in the attached word doc

Industry/Entity Type

Requirements
Must have
• All instructions and content are in the attached word doc
Nice to have
Should not have

```html
<!DOCTYPE html>
<html lang="en">
<head>
<meta charset="utf-8">
<title>Bayview Park Exposed – Flyer</title>
<link rel="stylesheet" href="https://fonts.googleapis.com/css2?family=Oswald:wght@500;600;700&family=Montserrat:wght@700;800;900&family=Outfit:wght@400;500;700;800&display=swap">
<style>
  :root{
    --stage:#262626;
    --red:#ee2a29;
    --yellow:#fff200;
    --ink:#3a1e1f;
    --white:#ffffff;
    --black:#111111;
  }
  *{margin:0;padding:0;box-sizing:border-box;}
  html,body{width:1200px;height:879px;overflow:hidden;background:var(--stage);}
  .stage{position:relative;width:1200px;height:879px;}
  .page{position:absolute;top:81px;width:555px;height:718px;background:var(--red);color:var(--white);overflow:hidden;}
  .page--front{left:30px;}
  .page--back{left:615px;}
  .abs{position:absolute;}
  .one-line{white-space:nowrap;}

  /* front page */
  .dateline{left:0;top:32px;width:459px;height:1.5px;background:var(--black);}
  .date{left:468px;top:24px;font:600 11px/1 "Oswald",sans-serif;color:var(--white);}
  .headline{left:0;width:555px;top:44px;text-align:center;font:700 50px/1 "Oswald",sans-serif;color:var(--yellow);letter-spacing:-0.3px;}
  .band{background:var(--ink);display:flex;align-items:center;justify-content:center;white-space:nowrap;}
  .band--kicker{left:32px;top:97px;width:489px;height:28px;font:800 19px/1 "Montserrat",sans-serif;letter-spacing:0.2em;}
  .subhead{left:0;width:555px;top:128px;text-align:center;font:800 27px/1.1 "Outfit",sans-serif;letter-spacing:-0.4px;}
  .photo{left:32px;top:173px;width:249px;height:140px;border:2px solid var(--white);background:linear-gradient(160deg,#9bbcd6 0%,#6d7f95 35%,#8a4c52 65%,#3b2c35 100%);}
  .rally{left:296px;top:172px;font:800 16px/1.2 "Montserrat",sans-serif;white-space:nowrap;}
  .rally em{font-style:normal;color:var(--yellow);}
  .rally-rule{left:296px;top:216px;width:112px;height:2px;background:var(--black);}
  .rally-copy{left:296px;top:225px;width:250px;font:700 13px/16.3px "Montserrat",sans-serif;}
  .pill{left:67px;top:325px;width:420px;height:34px;border-radius:8px;font:900 17px/1 "Montserrat",sans-serif;color:var(--yellow);}
  .meeting{left:0;width:555px;top:362px;text-align:center;font:600 30px/1.2 "Oswald",sans-serif;}
  .when{left:0;width:555px;top:401px;text-align:center;font:800 21px/1.1 "Montserrat",sans-serif;}
  .when b{color:var(--yellow);}
  .where{left:0;width:555px;top:428px;text-align:center;font:800 12.5px/1.1 "Montserrat",sans-serif;}
  .rallycry{width:555px;left:0;text-align:center;white-space:nowrap;}
  .rallycry__main{font:700 28px/1 "Oswald",sans-serif;color:var(--yellow);}
  .rallycry__sub{font:800 17px/1.2 "Outfit",sans-serif;margin-top:5px;letter-spacing:-0.2px;}
  .front-cry{top:455px;}
  .lawbook{left:33px;top:516px;width:157px;height:104px;border:2px solid var(--white);background:linear-gradient(120deg,#2f5a8a 0%,#3b6796 45%,#a56a3f 70%,#5a2a20 100%);}
  .band--lawsuit{left:203px;top:521px;width:310px;height:26px;font:800 14px/1 "Outfit",sans-serif;}
  .lawsuit-copy{left:203px;top:557px;width:345px;font:700 10.4px/13px "Montserrat",sans-serif;}
  .site{left:0;width:555px;top:640px;text-align:center;font:700 46px/1.2 "Oswald",sans-serif;color:var(--yellow);letter-spacing:-0.3px;white-space:nowrap;}

  /* back page */
  .intro{left:33px;top:30px;width:489px;font:500 11.6px/14px "Outfit",sans-serif;text-align:justify;}
  .intro b{color:var(--yellow);font:800 13px/1 "Montserrat",sans-serif;}
  .band--know{left:33px;top:93px;width:453px;height:34px;font:800 21px/1 "Outfit",sans-serif;letter-spacing:-0.2px;}
  .facts{left:33px;top:133px;width:489px;display:flex;flex-direction:column;gap:8px;}
  .fact h3{font:800 11px/1.2 "Montserrat",sans-serif;color:var(--yellow);white-space:nowrap;letter-spacing:-0.1px;}
  .fact p{font:500 11.5px/14px "Outfit",sans-serif;margin-top:1px;}
  .back-cry{top:593px;}
  .back-cry .rallycry__main{font:800 19px/1.1 "Outfit",sans-serif;}
  .back-cry .rallycry__sub{font:800 18.5px/1.1 "Outfit",sans-serif;margin-top:3px;}
</style>
</head>
<body>
<div class="stage">

  <section class="page page--front">
    <div class="abs dateline"></div>
    <div class="abs date">MAY 14, 2025</div>
    <h1 class="abs headline one-line">BAYVIEW PARK EXPOSED</h1>
    <div class="abs band band--kicker">DISABLED CHILD TRAUMATIZED</div>
    <h2 class="abs subhead one-line">PUBLIC LAND ABUSED FOR PROFIT</h2>
    <div class="abs photo" role="img" aria-label="Photo of a packed beachfront concert crowd with a performer in a blue cowboy hat at the Liberty Bash event"></div>
    <p class="abs rally">HELP <em>OUR BEACH<br>COMMUNITY</em> FIGHT BACK</p>
    <div class="abs rally-rule"></div>
    <p class="abs rally-copy">BAYVIEW PARK IS NOT PRIVATE. IT IS PUBLIC PROPERTY OWNED BY THE CITY, PAID FOR BY YOU.</p>
    <div class="abs band pill">JOIN US &amp; SHOW YOUR SUPPORT @</div>
    <p class="abs meeting one-line">MARINA BEACH TOWN COUNCIL MEETING</p>
    <p class="abs when one-line"><b>DATE:</b> MAY 14, 2025 – 6:00 PM</p>
    <p class="abs where one-line">PLACE: BAYVIEW PARK COMMUNITY ROOM (ABOVE THE ARCADE)</p>
    <div class="abs rallycry front-cry">
      <p class="rallycry__main">HELP OUR COMMUNITY SAVE BAYVIEW PARK</p>
      <p class="rallycry__sub">BAYVIEW PARK WAS BUILT FOR FAMILIES — NOT RAVES</p>
    </div>
    <div class="abs lawbook" role="img" aria-label="Illustration of a blue class action law book with scales of justice beside a wooden gavel"></div>
    <div class="abs band band--lawsuit">CLASS ACTION LAWSUIT FORMING NOW!</div>
    <p class="abs lawsuit-copy">IF YOU’VE BEEN IMPACTED BY NOISE, DENIED PUBLIC ACCESS, OR HARMED BY THESE VIOLATIONS, YOU MAY BE ELIGIBLE FOR COMPENSATION. WE’RE GATHERING STORIES AND PREPARING LEGAL ACTION.</p>
    <p class="abs site">WWW.FIXBAYVIEWPARK.COM</p>
  </section>

  <section class="page page--back">
    <p class="abs intro"><b>EXPOSED:</b> Marco Venturi, CEO of Coral Asset Group IX LLC the leaseholder of Bayview Park, has drawn community outrage for profiting off public land while operating Bayview Park in ways many say violate its lease and damage our beach, our peace, and our environment — all from his luxury estate in Oak Hollow Ridge.</p>
    <div class="abs band band--know">WHAT THEY DON’T WANT YOU TO KNOW:</div>

    <div class="abs facts">
      <div class="fact">
        <h3>ILLEGAL RAVES - NO PERMITS.</h3>
        <p>Explosive concerts over 100 decibels, blasting Marina Beach with bass — multiple times per week. According to Public Records these events had NO PERMITS &amp; NO CITY APPROVAL.</p>
      </div>
      <div class="fact">
        <h3>THE BEACH HOUSE ISN’T THEIRS - IT’S YOURS.</h3>
        <p>Bayview Park is shutting down public space for 9 private Beach House raves through July. But July 5 is different — “Liberty Bash” is a full-park, alcohol-fueled rave that shuts out the public from taxpayer-owned land. These takeovers appear to violate their lease and Prop G, which protects YOUR beach for ALL — not just paying partiers.</p>
      </div>
      <div class="fact">
        <h3>DISABLED CHILD TRAUMATIZED BY RAVE NOISE</h3>
        <p>A child with cerebral palsy and auditory sensitivity came to use the City’s Beach Accessibility Program but was overwhelmed by deafening Rave noise and fled in distress. The illegal sound levels deny All individuals with similar disabilities access to public accommodations. This is a direct violation of the Americans with Disabilities Act.</p>
      </div>
      <div class="fact">
        <h3>EXPOSED: IS BAYVIEW RUNNING AN UNETHICAL SELF-DEALING SCHEME ?</h3>
        <p>Bayview Park’s General Manager, Glen Porter, is also CEO of Shoreguard Security Group — the very company hired by Bayview for “security” services. And who’s listed as corporate secretary? Carla Venturi, close relative of the leaseholder Marco Venturi. Is this Self-Dealing?</p>
      </div>
      <div class="fact">
        <h3>DOCUMENTED RUNOFF AND SUSPECTED ENVIRONMENTAL DISASTER</h3>
        <p>Improperly Stored Chemicals, oils, and waste water spilling into storm drains. Parking lots are trashed, flooded, and neglected. Stormwater compliance appears to be ignored.</p>
      </div>
      <div class="fact">
        <h3>EXPOSED: BAYVIEW PARK’S ILLEGAL SIGNS MISLEAD THE PUBLIC.</h3>
        <p>They’re tricking the public into believing city-owned land is private, violating their lease which requires signage clearly stating the property is city-owned and open to all.</p>
      </div>
      <div class="fact">
        <h3>BAYVIEW PARK: ACCIDENT WAITING TO HAPPEN?</h3>
        <p>From the Big Comet to the rides and walkways, safety appears ignored. The lease requires independent engineer inspections — yet no reports can be found. With what looks like hundreds of code violations, the entire park may be one broken bolt from disaster. Who’s protecting the public?</p>
      </div>
    </div>

    <div class="abs rallycry back-cry">
      <p class="rallycry__main">HELP OUR COMMUNITY SAVE BAYVIEW PARK</p>
      <p class="rallycry__sub">BAYVIEW PARK WAS BUILT FOR FAMILIES — NOT RAVES</p>
    </div>
    <p class="abs site">WWW.FIXBAYVIEWPARK.COM</p>
  </section>

</div>
</body>
</html>
```